Design a web site for my business - Brightline Coatings Co.

We are a family business that handles design, fabrication and installation of powder coated aluminum, stainless steel and glass products. Including handrails, privacy slat screens, electric gates and pool fencing. We are based in the Whitsundays in North Queensland and service an area from Airlie Beach to Townsville.

Target Market(s)

Domestic and commercial

Industry/Entity Type

fabrication - manufacturing

Coding

Coded - Design and coding required

Number of Pages Required

5+ page

Colors
0054AA
0677BA
7BADD7
CADEEF
E8F1F8

Requirements
Must have
• photo galleries, contact page, one page for privacy screens, balustrades, glass fencing, stainless steel handrail, powder coated aluminium handrails and pool fencing

```html
<!DOCTYPE html>
<html lang="en">
<head>
<meta charset="utf-8">
<title>Brightline Coatings Co — Expert Custom Fabrication</title>
<link href="https://fonts.googleapis.com/css2?family=Unbounded:wght@500;600;700&family=Poppins:wght@400;500;600&display=swap" rel="stylesheet">
<style>
:root{
  --blue:#0054AA;
  --blue-mid:#0677BA;
  --blue-soft:#7BADD7;
  --blue-pale:#CADEEF;
  --blue-mist:#E8F1F8;
  --ink:#1b1d22;
  --muted:#5d6470;
  --grey-bg:#f1f2f4;
  --map-grey:#eef0f2;
  --footer:#1e1f22;
  --white:#ffffff;
}
*{margin:0;padding:0;box-sizing:border-box}
html,body{width:1200px;height:5352px;overflow:hidden}
body{position:relative;font-family:"Poppins",sans-serif;color:var(--ink);background:var(--white)}
.abs{position:absolute}
.display{font-family:"Unbounded",sans-serif;font-weight:700;text-transform:uppercase;letter-spacing:.5px}
.eyebrow{font-size:10px;text-transform:uppercase;letter-spacing:.5px}
.photo{position:absolute}
.read-more{font-size:10px;font-weight:600;color:var(--blue);text-decoration:underline;display:flex;align-items:center;gap:6px}
.btn{position:absolute;display:flex;align-items:center;justify-content:space-between;padding:0 20px;font-size:10px;font-weight:600;text-transform:uppercase}
.btn-blue{background:var(--blue);color:var(--white)}
.arrow-btn{position:absolute;width:38px;height:38px;display:flex;align-items:center;justify-content:center}

/* hero */
.hero{position:absolute;left:0;top:0;width:1200px;height:648px;background:linear-gradient(150deg,#1d2a1e 0%,#3a3b2f 40%,#5a4a3b 62%,#6d6b62 80%,#2e3a2c 100%)}
.hero-shade{position:absolute;inset:0;background:linear-gradient(90deg,rgba(0,0,0,.55),rgba(0,0,0,.1) 60%)}
.brand{color:var(--white);font-size:12px;font-weight:600;line-height:1.25;text-transform:uppercase}
.nav a{position:absolute;top:24px;color:var(--white);font-size:10px;font-weight:500;text-transform:uppercase;text-decoration:none}
.nav a.active{text-decoration:underline}
.hero-title{left:228px;top:186px;color:var(--white);font-size:52px;line-height:56px}
.hero-sub{left:230px;top:360px;color:var(--white);font-size:15px;font-weight:500;text-transform:uppercase}
.rule-v{left:178px;top:0;width:1px;height:648px;background:rgba(255,255,255,.25)}
.rule-h{left:0;top:498px;width:1200px;height:1px;background:rgba(255,255,255,.25)}
.touch{left:34px;top:566px;color:var(--white);font-size:10px;line-height:14px}

/* services */
.services-band{left:0;top:648px;width:1200px;height:415px;background:linear-gradient(90deg,var(--blue) 0%,var(--blue-mid) 100%)}
.section-head .eyebrow{color:var(--blue-pale)}
.section-head h2{font-size:30px;color:var(--white);margin-top:4px}
.service-card{position:absolute;top:851px;width:227px}
.service-card .photo{position:relative;width:227px;height:264px}
.service-card h3{font-family:"Unbounded",sans-serif;font-weight:600;font-size:11px;text-transform:uppercase;margin-top:27px}
.service-card p{font-size:9px;line-height:13px;color:var(--muted);margin-top:9px;height:28px}
.service-card .read-more{margin-top:12px}

/* process */
.step{left:228px;font-size:30px;line-height:36px}
.step.outline{color:transparent;-webkit-text-stroke:1.2px var(--blue)}
.step-rule{left:228px;width:478px;height:1px;background:#d7dbe0}
.process-name{left:776px;top:1380px;width:190px;font-family:"Poppins",sans-serif;font-weight:600;font-size:20px;line-height:26px;color:var(--blue);text-transform:uppercase}
.process-text{left:776px;top:1496px;width:260px;font-size:9px;line-height:15px;color:var(--muted)}

/* about */
.about-bg{left:0;top:1842px;width:1200px;height:618px;background:var(--grey-bg)}
.about-head{left:228px;top:1905px}
.about-head .eyebrow{color:#8b929c}
.about-head h2{font-size:30px;line-height:35px;margin-top:8px}
.about-copy{left:228px;top:2048px;width:362px;font-size:9.5px;line-height:15px;color:#3c424b}
.about-copy p+p{margin-top:15px}
.year-box{left:650px;top:2138px;width:110px;height:84px;background:rgba(20,30,40,.45);color:var(--white);font-size:32px;line-height:34px;padding:9px 0 0 24px}
.partner{position:absolute;top:2324px;width:96px;height:62px;border:2px solid #b9bec6;border-radius:6px}

/* work */
.work-band{left:0;top:2460px;width:1200px;height:635px;background:linear-gradient(90deg,var(--blue) 0%,var(--blue-mid) 100%)}
.work-caption{left:241px;top:3002px;width:288px;height:93px;background:rgba(10,14,20,.6);color:var(--white);padding:22px 34px}
.work-caption h3{font-family:"Unbounded",sans-serif;font-weight:600;font-size:11px;text-transform:uppercase}
.work-caption p{font-size:9px;line-height:13px;margin-top:10px;opacity:.9}

/* reach */
.map{left:190px;top:3276px;width:850px;height:300px;background:var(--map-grey)}
.reach-title{left:228px;top:3194px;font-size:30px;line-height:35px}
.stat{position:absolute;top:3588px}
.stat .num{font-family:"Unbounded",sans-serif;font-weight:700;font-size:50px;line-height:54px;color:var(--blue)}
.stat .label{font-size:9px;font-weight:600;line-height:11px;text-transform:uppercase;color:#2a2f36}

/* blog */
.blog-band{left:0;top:3751px;width:1200px;height:432px;background:linear-gradient(90deg,var(--blue) 0%,var(--blue-mid) 100%)}
.btn-outline{background:var(--white);color:var(--ink)}
.post{position:absolute;top:3920px;width:227px}
.post .photo{position:relative;width:227px;height:259px}
.post .tag{position:absolute;left:8px;bottom:0;background:var(--white);color:var(--blue);font-size:8px;font-weight:600;padding:4px 12px}
.post .date{font-size:8.5px;color:#8b929c;margin-top:26px}
.post h3{font-family:"Unbounded",sans-serif;font-weight:600;font-size:11px;line-height:16px;text-transform:uppercase;margin-top:6px}
.post .read-more{margin-top:12px}

/* testimonial */
.quote{left:200px;top:4510px;width:800px;text-align:center;font-size:31px;line-height:41px;font-weight:500;color:#1b1d22}
.reviewer{left:0;top:4642px;width:1200px;text-align:center;font-size:13px;font-weight:600}
.reviewer span{color:#f2a81d;letter-spacing:1px}
.dots{left:531px;top:4704px;display:flex;gap:6px}
.dots i{display:block;width:30px;height:4px;background:#d7dbe0;border-radius:2px}
.dots i.on{background:var(--ink)}

/* fence + footer */
.fence{left:0;top:4754px;width:1200px;height:198px;background:linear-gradient(180deg,rgba(30,31,34,.0) 0%,rgba(30,31,34,.35) 35%,rgba(30,31,34,.85) 100%)}
.footer{left:0;top:4951px;width:1200px;height:401px;background:var(--footer);color:var(--white)}
.footer-brand{left:128px;top:5140px;font-size:15px;font-weight:600;line-height:18px;text-transform:uppercase}
.footer-col{position:absolute;top:5052px}
.footer-col h4{font-family:"Unbounded",sans-serif;font-weight:600;font-size:12px;text-transform:uppercase;margin-bottom:18px}
.footer-col li{list-style:none;font-size:9px;line-height:20px;color:#c9ccd2}
.footer-col .k{font-size:8px;font-weight:600;text-transform:uppercase;color:var(--white);margin-top:4px}
.footer-col .v{font-size:9px;line-height:12px;color:#c9ccd2;margin-bottom:10px}
.field{width:210px;height:30px;background:#2e3035;font-size:8px;color:#9da2aa;padding:10px 14px;margin-top:10px}
.submit{width:210px;height:30px;background:var(--blue);font-size:9px;font-weight:600;display:flex;align-items:center;justify-content:center;gap:90px;margin-top:8px}
.copyright{left:0;top:5316px;width:1200px;text-align:center;font-size:8px;color:#c9ccd2}
</style>
</head>
<body>

<!-- HERO -->
<section class="hero">
  <div class="photo" style="inset:0" role="img" aria-label="Timber boardwalk with metal balustrade winding past boulders and tropical plants"></div>
  <div class="hero-shade"></div>
  <div class="abs rule-v"></div>
  <div class="abs rule-h"></div>
  <div class="abs brand" style="left:34px;top:82px">Brightline<br>Coatings Co</div>
  <nav class="nav">
    <a class="active" style="left:228px">Home</a>
    <a style="left:286px">Services</a>
    <a style="left:357px">Gallery</a>
    <a style="left:425px">About us</a>
    <a style="left:498px">Contact</a>
    <a style="left:600px">Request a free quote</a>
  </nav>
  <div class="abs" style="left:1138px;top:0;width:62px;height:62px;background:var(--blue);display:flex;flex-direction:column;align-items:center;justify-content:center;gap:5px">
    <i style="display:block;width:16px;height:1.5px;background:#fff"></i><i style="display:block;width:16px;height:1.5px;background:#fff"></i><i style="display:block;width:16px;height:1.5px;background:#fff"></i>
  </div>
  <h1 class="abs display hero-title">Expert<br>Custom<br>Fabrication</h1>
  <p class="abs hero-sub">For the Whitsundays and beyond.</p>
  <svg class="abs" style="left:36px;top:526px" width="30" height="30" viewBox="0 0 24 24" fill="none" stroke="#fff" stroke-width="1.8"><path d="M5 4h4l2 5-2.5 1.5a11 11 0 0 0 5 5L15 13l5 2v4a2 2 0 0 1-2 2A16 16 0 0 1 3 6a2 2 0 0 1 2-2z"/></svg>
  <div class="abs touch"><b style="text-transform:uppercase;font-weight:600">Get in touch</b><br><span style="display:block;margin-top:8px">+61 400 118 522</span>hello@brightlinecoatings.example</div>
  <a class="btn btn-blue" style="left:230px;top:552px;width:191px;height:44px">Get a free quote
    <svg width="14" height="10" viewBox="0 0 14 10" fill="none" stroke="#fff" stroke-width="1.4"><path d="M0 5h13M9 1l4 4-4 4"/></svg></a>
  <div class="abs" style="left:430px;top:552px;width:44px;height:44px;background:#fff;display:flex;align-items:center;justify-content:center">
    <svg width="10" height="10" viewBox="0 0 10 10"><path d="M2 1l7 4-7 4z" fill="#111"/></svg></div>
</section>

<!-- SERVICES -->
<div class="abs services-band"></div>
<div class="abs section-head" style="left:230px;top:752px">
  <p class="eyebrow">What we offer</p>
  <h2 class="display">Our services</h2>
</div>
<div class="arrow-btn" style="left:882px;top:768px;background:#fff"><svg width="14" height="10" viewBox="0 0 14 10" fill="none" stroke="#111" stroke-width="1.4"><path d="M14 5H1M5 1L1 5l4 4"/></svg></div>
<div class="arrow-btn" style="left:927px;top:768px;background:rgba(255,255,255,.15)"><svg width="14" height="10" viewBox="0 0 14 10" fill="none" stroke="#fff" stroke-width="1.4"><path d="M0 5h13M9 1l4 4-4 4"/></svg></div>

<article class="service-card" style="left:230px">
  <div class="photo" style="background:linear-gradient(180deg,#3b7fd0 0%,#8fb9e6 45%,#e7e6e1 46%,#cfcbc3 100%)" role="img" aria-label="White aluminium privacy slat screen gate against a blue sky"></div>
  <h3>Privacy slat screens</h3>
  <p>Modern powder coated aluminium privacy screens that provide security, airflow...</p>
  <a class="read-more">Read more <svg width="12" height="8" viewBox="0 0 14 10" fill="none" stroke="currentColor" stroke-width="1.5"><path d="M0 5h13M9 1l4 4-4 4"/></svg></a>
</article>
<article class="service-card" style="left:484px">
  <div class="photo" style="background:linear-gradient(160deg,#4d5a43 0%,#6b5a47 40%,#8a6848 70%,#3a4036 100%)" role="img" aria-label="Timber deck with dark balustrade overlooking a rocky creek"></div>
  <h3>Balustrades</h3>
  <p>Custom aluminium, stainless steel and glass balustrades designed to enhance safety...</p>
  <a class="read-more">Read more <svg width="12" height="8" viewBox="0 0 14 10" fill="none" stroke="currentColor" stroke-width="1.5"><path d="M0 5h13M9 1l4 4-4 4"/></svg></a>
</article>
<article class="service-card" style="left:739px">
  <div class="photo" style="background:linear-gradient(170deg,#3f6b3c 0%,#6e8d66 45%,#a9afa6 75%,#8c8e88 100%)" role="img" aria-label="Frameless glass fence along a garden path with tropical plants"></div>
  <h3>Glass fencing</h3>
  <p>Frameless and semi-frameless glass fencing that creates a clean, open look for pools...</p>
  <a class="read-more">Read more <svg width="12" height="8" viewBox="0 0 14 10" fill="none" stroke="currentColor" stroke-width="1.5"><path d="M0 5h13M9 1l4 4-4 4"/></svg></a>
</article>
<article class="service-card" style="left:993px">
  <div class="photo" style="background:linear-gradient(170deg,#b9c4c9 0%,#7f8c7a 45%,#6f5b4a 75%,#4c3f35 100%)" role="img" aria-label="Stainless steel handrail along a timber boardwalk"></div>
  <h3 style="white-space:nowrap">Stainless steel handrails</h3>
  <p>Durable stainless steel handrails designed for residential, commercial and public spaces.</p>
  <a class="read-more">Read more <svg width="12" height="8" viewBox="0 0 14 10" fill="none" stroke="currentColor" stroke-width="1.5"><path d="M0 5h13M9 1l4 4-4 4"/></svg></a>
</article>

<!-- PROCESS -->
<div class="abs display step" style="top:1352px">01. Consultation</div>
<div class="abs step-rule" style="top:1407px"></div>
<div class="abs display step outline" style="top:1430px">02. Design &amp; Quote</div>
<div class="abs step-rule" style="top:1486px"></div>
<div class="abs display step" style="top:1507px">03. Fabrication</div>
<div class="abs step-rule" style="top:1561px"></div>
<div class="abs display step" style="top:1584px">04. Installation</div>
<div class="abs process-name">Brightline<br>Coatings Co</div>
<p class="abs process-text">After understanding your requirements, we prepare a customised design and provide a clear, transparent quotation. Every solution is tailored to suit your style, budget and project specifications.</p>
<a class="btn btn-blue" style="left:776px;top:1590px;width:191px;height:42px">Get a free quote
  <svg width="14" height="10" viewBox="0 0 14 10" fill="none" stroke="#fff" stroke-width="1.4"><path d="M0 5h13M9 1l4 4-4 4"/></svg></a>

<!-- ABOUT -->
<div class="abs about-bg"></div>
<div class="photo" style="left:650px;top:1763px;width:550px;height:500px;background:linear-gradient(180deg,#d9dde0 0%,#c4ccd0 35%,#e9ecec 50%,#77b3c4 68%,#4d7a4a 85%,#3f5e37 100%)" role="img" aria-label="Modern white residence with curved roof beside a resort pool and black pool fence"></div>
<div class="abs year-box display">19<br>95</div>
<div class="abs about-head">
  <p class="eyebrow">About us</p>
  <h2 class="display">Quality<br>craftsmanship,<br>family values.</h2>
</div>
<div class="abs about-copy">
  <p>We specialise in designing, fabricating and installing premium aluminium, stainless steel and glass products that combine functionality, durability and modern style.</p>
  <p>From privacy screens and custom handrails to electric gates and pool fencing, every project is completed with attention to detail and built to withstand Australia's harsh climate.</p>
  <p>Whether it's a single residential installation or a large commercial project, our experienced team is committed to delivering exceptional workmanship from concept through to completion.</p>
</div>
<div class="partner" style="left:220px"></div>
<div class="partner" style="left:372px;border-radius:50%"></div>
<div class="partner" style="left:540px"></div>
<div class="partner" style="left:710px;border-radius:50%"></div>
<div class="partner" style="left:884px"></div>

<!-- WORK -->
<div class="abs work-band"></div>
<div class="abs section-head" style="left:215px;top:2540px">
  <p class="eyebrow">Portfolio projects</p>
  <h2 class="display">See our work</h2>
</div>
<div class="arrow-btn" style="left:868px;top:2555px;background:#fff"><svg width="14" height="10" viewBox="0 0 14 10" fill="none" stroke="#111" stroke-width="1.4"><path d="M14 5H1M5 1L1 5l4 4"/></svg></div>
<div class="arrow-btn" style="left:913px;top:2555px;background:rgba(255,255,255,.15)"><svg width="14" height="10" viewBox="0 0 14 10" fill="none" stroke="#fff" stroke-width="1.4"><path d="M0 5h13M9 1l4 4-4 4"/></svg></div>
<div class="photo" style="left:0;top:2653px;width:220px;height:442px;background:linear-gradient(170deg,#3c5a3a 0%,#6d8767 50%,#8f948e 100%)" role="img" aria-label="Frameless glass pool fence beside garden palms"></div>
<div class="photo" style="left:241px;top:2653px;width:718px;height:442px;background:linear-gradient(180deg,#e4e7ea 0%,#d4d8da 35%,#8a8c8a 55%,#2f3236 75%,#6d7a5c 100%)" role="img" aria-label="Queenslander home with black slat fence and gate"></div>
<div class="photo" style="left:978px;top:2653px;width:222px;height:442px;background:linear-gradient(180deg,#dfe7ee 0%,#7c9474 35%,#4f6f8a 60%,#8a6a4e 85%,#5a4535 100%)" role="img" aria-label="Waterfront balustrade overlooking rocks and sea"></div>
<div class="abs work-caption">
  <h3>Glass fencing</h3>
  <p>Frameless and semi-frameless glass fencing that creates a clean, open look for pools...</p>
</div>
<div class="abs" style="left:523px;top:3001px;width:8px;height:8px;background:var(--blue-mid)"></div>

<!-- REACH -->
<div class="abs map" role="img" aria-label="World map marked with blue location pins showing where projects have been delivered"></div>
<h2 class="abs display reach-title">Proudly servicing<br>North Queensland</h2>
<div class="stat" style="left:247px"><div class="num">25</div><div class="label">Years of<br>experience</div></div>
<div class="stat" style="left:448px"><div class="num">8K</div><div class="label">Skilled<br>professionals</div></div>
<div class="stat" style="left:656px"><div class="num">32</div><div class="label">Visited<br>conferences</div></div>
<div class="stat" style="left:872px"><div class="num">1K</div><div class="label">Project<br>worldwide</div></div>

<!-- BLOG -->
<div class="abs blog-band"></div>
<div class="abs section-head" style="left:230px;top:3822px">
  <p class="eyebrow">Latest article</p>
  <h2 class="display" style="word-spacing:8px">Lastest blog post</h2>
</div>
<a class="btn btn-outline" style="left:776px;top:3830px;width:191px;height:42px">Explore more
  <svg width="14" height="10" viewBox="0 0 14 10" fill="none" stroke="#111" stroke-width="1.4"><path d="M0 5h13M9 1l4 4-4 4"/></svg></a>

<article class="post" style="left:230px">
  <div class="photo" style="background:linear-gradient(180deg,#e6e6e3 0%,#b9b8b2 40%,#5a4a3c 75%,#3b3731 100%)" role="img" aria-label="Louvred aluminium patio roof"><span class="tag">Experience</span></div>
  <p class="date">August 20, 2024</p>
  <h3>Reliable service you<br>can count on</h3>
  <a class="read-more">Read more <svg width="12" height="8" viewBox="0 0 14 10" fill="none" stroke="currentColor" stroke-width="1.5"><path d="M0 5h13M9 1l4 4-4 4"/></svg></a>
</article>
<article class="post" style="left:484px">
  <div class="photo" style="background:linear-gradient(180deg,#c8bcb0 0%,#d9d5ce 35%,#4a4a4a 60%,#2b2c2e 80%,#6b7a57 100%)" role="img" aria-label="House with black slat fence at dusk"><span class="tag">Quality</span></div>
  <p class="date">December 15, 2024</p>
  <h3>Reliable service you<br>can count on</h3>
  <a class="read-more">Read more <svg width="12" height="8" viewBox="0 0 14 10" fill="none" stroke="currentColor" stroke-width="1.5"><path d="M0 5h13M9 1l4 4-4 4"/></svg></a>
</article>
<article class="post" style="left:739px">
  <div class="photo" style="background:linear-gradient(180deg,#a7c8e6 0%,#e8e6e0 40%,#8a7864 65%,#5d6b4a 100%)" role="img" aria-label="Home entrance with powder coated screens"><span class="tag">Company</span></div>
  <p class="date">November 20, 2024</p>
  <h3>Reliable service you<br>can count on</h3>
  <a class="read-more">Read more <svg width="12" height="8" viewBox="0 0 14 10" fill="none" stroke="currentColor" stroke-width="1.5"><path d="M0 5h13M9 1l4 4-4 4"/></svg></a>
</article>

<!-- TESTIMONIAL -->
<svg class="abs" style="left:572px;top:4430px" width="56" height="44" viewBox="0 0 56 44" fill="var(--blue)">
  <path d="M0 24C0 10 8 2 20 0l2 6C15 9 12 14 12 20h10v24H0z"/>
  <path d="M32 24C32 10 40 2 52 0l2 6c-7 3-10 8-10 14h10v24H32z"/>
</svg>
<p class="abs quote">"We couldn't be happier with our new glass pool fencing.Professional service, quality workmanship and completed on schedule."</p>
<p class="abs reviewer">Daniel M <span>★★★★★</span></p>
<div class="abs dots"><i></i><i></i><i class="on"></i><i></i></div>

<!-- FENCE + FOOTER -->
<div class="abs fence" role="img" aria-label="Silhouette of an ornate black picket fence"></div>
<footer class="abs footer"></footer>
<div class="abs footer-brand" style="color:#fff">Brightline<br>Coatings Co</div>
<div class="footer-col" style="left:357px;color:#fff">
  <h4>Quick links</h4>
  <ul><li>Home</li><li>About Us</li><li>Services</li><li>Projects</li><li>Our Process</li><li>Contact</li></ul>
</div>
<div class="footer-col" style="left:519px;color:#fff">
  <h4>Help</h4>
  <ul><li>Help center</li><li>FAQs</li><li>Privacy policy</li><li>Cookie policy</li><li>Terms of use</li><li>Cookie settings</li></ul>
</div>
<div class="footer-col" style="left:658px;color:#fff">
  <h4>Contact us</h4>
  <p class="k">Website :</p>
  <p class="v">12 Harbour View Rd, Cannonvale,<br>QLD Australia, Queensland</p>
  <p class="k">Phone :</p>
  <p class="v">+61 400 118 522</p>
  <p class="k">Mail us :</p>
  <p class="v">hello@brightlinecoatings.example</p>
</div>
<div class="footer-col" style="left:857px;color:#fff">
  <h4>Newsletter</h4>
  <p style="font-size:8px;font-weight:600">Subscribe our mailing list</p>
  <div class="field">Email...</div>
  <div class="submit"><span>SUBMIT</span>
    <svg width="12" height="12" viewBox="0 0 12 12" fill="#fff"><path d="M12 0L0 5l5 2 2 5z"/></svg></div>
</div>
<p class="abs copyright">© 2025 Brightline Coatings Co | All rights reserved</p>

</body>
</html>
```